Transform Your Giving

I need a tri-fold brochure that will fit in a standard number 10 business envelope. Meadowlark and Allied Services is a charitable nonprofit. The goal of this brochure is to stimulate people into thinking about other ways to make a donation. The design should communicate the essential information on donation options, create a sense of professional integrity, be graphically sharp, easy to read and laid out in a way that doesn't make the material appear crowded.

```html
<!DOCTYPE html>
<html lang="en">
<head>
<meta charset="utf-8">
<title>Transform Your Giving – Meadowlark and Allied Services Brochure</title>
<link rel="stylesheet" href="https://fonts.googleapis.com/css2?family=Fira+Sans:ital,wght@0,300;0,400;0,500;0,600;0,700;1,300;1,600;1,700&display=swap">
<style>
:root{
  --navy:#2c2a73;
  --green:#4cb944;
  --ink:#232323;
  --backdrop:#777777;
  --white:#ffffff;
  --muted:#b9b9bd;
}
*{box-sizing:border-box;margin:0;padding:0}
html,body{width:1096px;height:1200px;overflow:hidden}
body{background:var(--backdrop);font-family:"Fira Sans",sans-serif;color:var(--ink);position:relative}
.spread{position:absolute;left:205px;width:687px;height:515px;display:flex;background:var(--white)}
.spread--outside{top:63px}
.spread--inside{top:621px}
.panel{position:relative;width:229px;height:515px;overflow:hidden}
.panel--navy{background:var(--navy);color:var(--white);text-align:center}
.panel--fold{background:linear-gradient(90deg,#fff 0,#fff 88%,#ececec 100%)}
.photo{position:absolute;left:0;width:100%}
.curve{position:absolute;left:0;width:100%;display:block}
.icon-defs{position:absolute;width:0;height:0}

/* outside panel 1 */
.photo--carer{top:0;height:262px;background:linear-gradient(135deg,#f2efe9 0%,#d8d2c7 45%,#b9ad9c 100%)}
.impact{position:absolute;left:18px;right:14px;top:277px}
.impact h2{font-size:12px;font-weight:700;color:var(--navy);letter-spacing:.1px;margin-bottom:2px}
.impact p{font-size:9.7px;line-height:12.9px;color:var(--ink)}
.checks{position:absolute;left:18px;top:408px;display:grid;grid-template-columns:59px 120px;row-gap:6px;font-size:10px;font-weight:500;color:var(--ink)}
.checks li{list-style:none;display:flex;align-items:center;gap:5px}
.tick{width:8px;height:8px;flex:none}
.wordmark{text-align:center;line-height:1}
.wordmark__name{font-weight:700;letter-spacing:1px;display:block}
.wordmark__line{font-weight:600;letter-spacing:.4px;display:block;margin-top:3px}
.wordmark--faint{position:absolute;left:90px;width:120px;top:465px;color:var(--muted)}
.wordmark--faint .wordmark__name{font-size:22px}
.wordmark--faint .wordmark__line{font-size:3.6px}

/* outside panel 2 */
.invite{position:absolute;left:16px;right:16px;top:17px;font-size:8.4px;font-weight:600;line-height:11.5px}
.quote{position:absolute;left:20px;right:20px;top:92px;font-size:8.6px;font-style:italic;font-weight:300;line-height:11.5px}
.photo--hands{top:140px;height:96px;background:linear-gradient(90deg,#e2a47d 0%,#f0c2a0 50%,#d99a72 100%);clip-path:polygon(0 38%,100% 0,100% 62%,0 100%)}
.will{position:absolute;left:10px;right:10px;top:224px;font-size:8.4px;line-height:11px}
.will a{color:var(--green);text-decoration:underline}
.wordmark--light{position:absolute;left:40px;right:40px;top:278px;color:var(--white)}
.wordmark--light .wordmark__name{font-size:30px}
.wordmark--light .wordmark__line{font-size:5px}
.contact{position:absolute;left:10px;right:10px;top:339px}
.contact h3{font-size:10.5px;font-weight:700;text-decoration:underline;margin-bottom:5px}
.contact__lead{font-size:8.5px;font-weight:600;color:var(--green);line-height:11.3px;margin-bottom:4px}
.contact__item{font-size:8px;font-weight:300;line-height:10.5px;margin-bottom:5px}
.contact__icon{display:block;margin:0 auto 2px;width:8px;height:8px}
.follow{position:absolute;left:0;right:0;top:489px;font-size:8.6px;font-weight:700;display:flex;justify-content:center;align-items:center;gap:3px}
.follow span{text-decoration:underline;margin-right:2px}
.social-dot{width:9px;height:9px;border-radius:50%;background:var(--green)}

/* outside panel 3 */
.cover-head{position:absolute;left:0;right:0;top:13px;text-align:center}
.cover-head h1{font-size:16.5px;font-weight:600;color:var(--navy);line-height:20px}
.cover-head .strap{font-size:16.5px;font-weight:700;color:var(--green);line-height:20px}
.cover-head p{font-size:8.5px;font-weight:600;color:var(--navy);line-height:11.3px;margin-top:6px}
.photo--couple{top:88px;height:208px;background:linear-gradient(160deg,#e9dcc0 0%,#d8c49d 40%,#bfae8d 70%,#f3d58a 100%)}
.options{position:absolute;left:0;width:229px}
.options--row1{top:289px}
.options--row2{top:349px}
.option{position:absolute;width:80px;text-align:center;font-size:10px;font-weight:600;color:var(--ink);line-height:13px}
.option svg{display:block;margin:0 auto 3px;width:43px;height:43px}
.options__link{position:absolute;border-top:1.5px dotted var(--navy);height:0}
.wordmark--cover{position:absolute;left:20px;right:20px;top:452px;color:var(--navy)}
.wordmark--cover .wordmark__name{font-size:34px}
.wordmark--cover .wordmark__line{font-size:5.4px}

/* inside */
.inner{position:absolute;left:18px;right:14px;top:16px}
.intro{font-size:8.8px;font-weight:500;line-height:11.5px;margin-bottom:6px}
.gift{display:grid;grid-template-columns:55px 1fr;align-items:start;margin-bottom:3px}
.gift svg{width:52px;height:52px}
.gift__title{font-size:9px;font-weight:700;color:var(--navy);line-height:11.5px}
.gift__lead{font-size:8.6px;font-weight:700;font-style:italic;color:var(--green);line-height:11.3px;margin-top:3px}
.body{font-size:8px;font-weight:300;line-height:10.9px;color:var(--ink)}
.how{font-size:10.4px;font-weight:600;color:var(--navy);margin:7px 0 1px}
.gap{height:14px}
.bullets{list-style:none;margin:8px 0 7px 0}
.bullets li{display:grid;grid-template-columns:10px 1fr;font-size:7.7px;font-weight:300;line-height:10.3px;margin-bottom:4px}
.bullets .tick{margin-top:1px}
.photo--grandfather{top:367px;height:148px;background:linear-gradient(120deg,#3f4a3e 0%,#6f7664 40%,#d8b7a1 75%,#a78d7c 100%)}
</style>
</head>
<body>

<svg class="icon-defs" aria-hidden="true">
  <defs>
    <symbol id="ic-tick" viewBox="0 0 10 10"><circle cx="5" cy="5" r="5" fill="#2c2a73"/><path d="M2.8 5.2 4.4 6.7 7.3 3.6" fill="none" stroke="#fff" stroke-width="1.4"/></symbol>
    <symbol id="ic-coin" viewBox="0 0 40 40"><circle cx="20" cy="20" r="10" fill="none" stroke="#fff" stroke-width="2"/><circle cx="20" cy="20" r="5.5" fill="none" stroke="#fff" stroke-width="1.5"/></symbol>
    <symbol id="ic-bank" viewBox="0 0 40 40"><g fill="none" stroke="#fff" stroke-width="1.6"><path d="M10 16 20 10 30 16Z"/><path d="M11 17h18M11 29h18M9 31h22M13 18v10M17.5 18v10M22.5 18v10M27 18v10"/></g></symbol>
    <symbol id="ic-gift" viewBox="0 0 40 40"><g fill="none" stroke="#fff" stroke-width="1.6"><rect x="11" y="17" width="18" height="13"/><rect x="10" y="13" width="20" height="4"/><path d="M20 13v17M20 13c-3-5-7-3-5 0M20 13c3-5 7-3 5 0"/></g></symbol>
    <symbol id="ic-chart" viewBox="0 0 40 40"><g fill="none" stroke="#fff" stroke-width="1.6"><rect x="11" y="23" width="4" height="7"/><rect x="17" y="20" width="4" height="10"/><rect x="23" y="17" width="4" height="13"/><path d="M10 20 17 14 21 16 29 10M25 10h4v4"/></g></symbol>
    <symbol id="ic-cal" viewBox="0 0 40 40"><g fill="none" stroke="#fff" stroke-width="1.5"><rect x="10" y="13" width="20" height="17" rx="1.5"/><path d="M10 18h20M14 11v4M26 11v4"/><circle cx="20" cy="13" r="3.5" fill="#2c2a73"/><path d="M13 22h3M13 26h3M19 22h3M19 26h3M25 22h2M25 26h2"/></g></symbol>
    <symbol id="badge-ring" viewBox="0 0 52 52"><circle cx="26" cy="26" r="25" fill="#fff" stroke="#4cb944" stroke-width="2.4"/><circle cx="26" cy="26" r="21" fill="#2c2a73"/></symbol>
    <symbol id="badge-thin" viewBox="0 0 52 52"><circle cx="26" cy="26" r="25" fill="#2c2a73"/><circle cx="26" cy="26" r="23" fill="none" stroke="#fff" stroke-width="1.3"/></symbol>
  </defs>
</svg>

<!-- Outside spread -->
<section class="spread spread--outside">

  <article class="panel panel--impact">
    <div class="photo photo--carer" role="img" aria-label="Photo of a young caregiver smiling with an elderly man at home"></div>
    <svg class="curve" style="top:240px" width="229" height="26" viewBox="0 0 229 26" preserveAspectRatio="none"><path d="M0 26 Q114 -4 229 26 Z" fill="#fff"/><path d="M0 25 Q114 -6 229 25" fill="none" stroke="#4cb944" stroke-width="3"/></svg>
    <div class="impact">
      <h2>THE IMPACT OF YOUR GIFT</h2>
      <p>Your generosity drives our mission. With every Smart gift you’re supporting Meadowlark and Allied Services. Join our community of Smart Givers today and make an enduring impact. With Smart Giving your generosity reaches further.&nbsp; Begin your Smart Giving journey with us today.</p>
    </div>
    <ul class="checks">
      <li><svg class="tick"><use href="#ic-tick"/></svg>DAFs</li>
      <li><svg class="tick"><use href="#ic-tick"/></svg>Stocks and Securities</li>
      <li><svg class="tick"><use href="#ic-tick"/></svg>QCDs</li>
      <li><svg class="tick"><use href="#ic-tick"/></svg>Charitable Annuity</li>
      <li><svg class="tick"><use href="#ic-tick"/></svg>Crypto</li>
    </ul>
    <div class="wordmark wordmark--faint"><span class="wordmark__name">MAS</span><span class="wordmark__line">MEADOWLARK AND ALLIED SERVICES, INC.</span></div>
  </article>

  <article class="panel panel--navy">
    <p class="invite">To learn more about Smart Giving Options and how they can benefit you and Meadowlark and Allied Services, please reach out to our team.&nbsp; We’re here to help you navigate these giving methods and answer any question you may have.</p>
    <p class="quote">Being kind to others is a way of<br>being good to yourself.<br>Miriam Ashford</p>
    <div class="photo photo--hands" role="img" aria-label="Photo of a younger hand gently holding an elderly hand"></div>
    <p class="will">If you do not have a will, go to<br><a>www.simplewillnow.org</a><br>In 20 minutes you can have a legal will – for free.</p>
    <div class="wordmark wordmark--light"><span class="wordmark__name">MAS</span><span class="wordmark__line">MEADOWLARK AND ALLIED SERVICES, INC.</span></div>
    <div class="contact">
      <h3>CONTACT US</h3>
      <p class="contact__lead">Have more question? Please contact us at Meadowlark and Allied Services</p>
      <svg class="contact__icon" viewBox="0 0 10 10"><circle cx="5" cy="5" r="5" fill="#4cb944"/><path d="M5 2.3a1.8 1.8 0 0 1 1.8 1.8C6.8 5.4 5 7.6 5 7.6S3.2 5.4 3.2 4.1A1.8 1.8 0 0 1 5 2.3Z" fill="#2c2a73"/></svg>
      <p class="contact__item">1220 Prairie View Ave.<br>Suite 2 Fargo, ND&nbsp; 58102</p>
      <svg class="contact__icon" viewBox="0 0 10 10"><circle cx="5" cy="5" r="5" fill="#4cb944"/><path d="M3.3 2.6 4.3 2.5 4.8 3.9 4.1 4.4Q4.6 5.5 5.6 5.9L6.1 5.2 7.5 5.7 7.4 6.7Q5.6 7.3 4.1 5.9 2.7 4.4 3.3 2.6Z" fill="#2c2a73"/></svg>
      <p class="contact__item">701-555-0142 (ext. 100)</p>
      <svg class="contact__icon" viewBox="0 0 10 10"><circle cx="5" cy="5" r="5" fill="#4cb944"/><rect x="2.6" y="3.3" width="4.8" height="3.4" fill="#2c2a73"/><path d="M2.6 3.3 5 5.2 7.4 3.3" fill="none" stroke="#4cb944" stroke-width=".6"/></svg>
      <p class="contact__item">dkeller@meadowlarkallied.org</p>
      <svg class="contact__icon" viewBox="0 0 10 10"><circle cx="5" cy="5" r="5" fill="#4cb944"/><g fill="none" stroke="#2c2a73" stroke-width=".6"><circle cx="5" cy="5" r="2.6"/><ellipse cx="5" cy="5" rx="1.1" ry="2.6"/><path d="M2.4 5h5.2"/></g></svg>
      <p class="contact__item">www.meadowlarkallied.org</p>
    </div>
    <div class="follow"><span>FOLLOW US:</span><i class="social-dot"></i><i class="social-dot"></i></div>
  </article>

  <article class="panel panel--cover">
    <header class="cover-head">
      <h1>Transform Your Giving</h1>
      <div class="strap">Be Strategic, Be Smart</div>
      <p>Discover the impact of Smart Giving with<br>Meadowlark and Allied Services</p>
    </header>
    <div class="photo photo--couple" role="img" aria-label="Photo of a smiling senior couple embracing outdoors in sunlight"></div>
    <svg class="curve" style="top:84px" width="229" height="22" viewBox="0 0 229 22" preserveAspectRatio="none"><path d="M0 0 H229 V22 Q114 -2 0 22 Z" fill="#fff"/><path d="M0 22 Q114 -4 229 22" fill="none" stroke="#4cb944" stroke-width="3"/></svg>
    <svg class="curve" style="top:274px" width="229" height="26" viewBox="0 0 229 26" preserveAspectRatio="none"><path d="M0 26 Q114 -4 229 26 Z" fill="#fff"/><path d="M0 25 Q114 -6 229 25" fill="none" stroke="#4cb944" stroke-width="3"/></svg>
    <div class="options options--row1">
      <i class="options__link" style="left:64px;width:37px;top:21px"></i>
      <i class="options__link" style="left:134px;width:30px;top:21px"></i>
      <div class="option" style="left:5px"><svg viewBox="0 0 52 52"><use href="#badge-thin"/><use href="#ic-coin" x="6" y="6" width="40" height="40"/></svg>CRYPTO</div>
      <div class="option" style="left:75px"><svg viewBox="0 0 52 52"><use href="#badge-thin"/><use href="#ic-bank" x="6" y="6" width="40" height="40"/></svg>DAF’S</div>
      <div class="option" style="left:143px"><svg viewBox="0 0 52 52"><use href="#badge-thin"/><use href="#ic-gift" x="6" y="6" width="40" height="40"/></svg>QCDS</div>
    </div>
    <div class="options options--row2">
      <i class="options__link" style="left:99px;width:31px;top:21px"></i>
      <div class="option" style="left:40px"><svg viewBox="0 0 52 52"><use href="#badge-thin"/><use href="#ic-chart" x="6" y="6" width="40" height="40"/></svg>STOCKS &amp;<br>SECURITIES</div>
      <div class="option" style="left:113px"><svg viewBox="0 0 52 52"><use href="#badge-thin"/><use href="#ic-cal" x="6" y="6" width="40" height="40"/></svg>CHARITABLE<br>ANNUITY</div>
    </div>
    <div class="wordmark wordmark--cover"><span class="wordmark__name">MAS</span><span class="wordmark__line">MEADOWLARK AND ALLIED SERVICES, INC.</span></div>
  </article>
</section>

<!-- Inside spread -->
<section class="spread spread--inside">

  <article class="panel panel--fold">
    <div class="inner">
      <p class="intro">We would like to introduce you to five Strategic and Smart ways to give that could potentially be more beneficial to you compared to traditional cash donations. We encourage you to keep this information as a guide for your future contributions.</p>
      <div class="gift">
        <svg viewBox="0 0 52 52"><use href="#badge-ring"/><use href="#ic-chart" x="6" y="6" width="40" height="40"/></svg>
        <div><h3 class="gift__title">Gifts of Stocks or Appreciated Assets Strategic &amp; Smart</h3><p class="gift__lead">Consider your long-term publicly traded stock as a way to give to your favorite charity.</p></div>
      </div>
      <p class="body">You can make a significantly bigger impact when you donate long-term appreciated securities, including stock, mutual funds, &amp; bonds, directly to your favorite charity.</p>
      <h4 class="how">How Does It Work?</h4>
      <p class="body">When you donate stock to a charity, you will generally take a tax deduction for the full market value. Because you are donating stock, your contribution &amp; tax deduction may be significantly higher than contributing the after-tax proceeds. The same benefits apply when you donate mutual funds or bonds.</p>
      <div class="gap"></div>
      <div class="gift">
        <svg viewBox="0 0 52 52"><use href="#badge-ring"/><use href="#ic-bank" x="6" y="6" width="40" height="40"/></svg>
        <div><h3 class="gift__title">Donor-Advised Fund (DAF)<br>Strategic &amp; Smart</h3><p class="gift__lead">Consider a DAF – a simple, flexible, and tax-advantageous way to give to your favorite charities.</p></div>
      </div>
      <p class="body">A Donor-Advised Fund (DAF), is like a charitable investment account for the sole purpose of supporting your favorite charities.</p>
      <h4 class="how">How Does It Work?</h4>
      <p class="body">You establish a DAF &amp; contribute cash, stocks, or non-publicly traded assets, cryptocurrency, &amp; private company stock to be eligible for an immediate tax deduction. Those funds are contributed for tax-free growth. You can recommend grants be made from your DAF to any IRS qualified public charity.</p>
    </div>
  </article>

  <article class="panel panel--fold">
    <div class="inner">
      <div class="gift">
        <svg viewBox="0 0 52 52"><use href="#badge-ring"/><use href="#ic-gift" x="6" y="6" width="40" height="40"/></svg>
        <div><h3 class="gift__title">Qualified Charitable Distributions (QCDs) Strategic &amp; Smart</h3><p class="gift__lead">Consider a QCD – when planning your IRA withdrawal strategy… &amp; donate to your favorite charity.</p></div>
      </div>
      <p class="body">IRA owners at age 70 ½ or over can transfer dollars from their IRA to charity tax-free each year. These transfers known as Qualified Charitable Distributions (QCDs) offer eligible older Americans a great way to easily give to charity.</p>
      <h4 class="how">How Does It Work?</h4>
      <p class="body">Are you 72 and required to take a minimum distribution (RMD) from your IRA but do not need the funds? Consider a Qualified Charitable Distribution. Normally, distributions from a traditional IRA are taxable when received. With a QCD, these distributions become tax-free when paid directly from the IRA to your favorite eligible charity. An IRA owner wishing to make a QCD should contact their IRA trustee, allowing time to complete the transaction before the end of the year to receive the tax benefit.</p>
      <div class="gap" style="height:20px"></div>
      <div class="gift">
        <svg viewBox="0 0 52 52"><use href="#badge-ring"/><use href="#ic-cal" x="6" y="6" width="40" height="40"/></svg>
        <div><h3 class="gift__title">Charitable Gift Annuity<br>Strategic &amp; Smart</h3><p class="gift__lead">Consider establishing a<br>Charitable Gift Annuity</p></div>
      </div>
      <p class="body" style="margin-top:4px">You make a donation to a single charity. The gift is set aside in a reserve account and invested.</p>
      <h4 class="how">How Does It Work?</h4>
      <p class="body">A charitable gift annuity is a contract between a donor &amp; a charity. As a donor, you make a sizable gift to charity using cash, securities, or possibly other assets. This money is then invested. In return, you become eligible to take a partial tax deduction for your donation, plus you receive a fixed stream of income from the charity for the rest of your life. At the end of your life (as well as your spouse’s, if you’re giving as a couple), the charity receives the remainder of the gift.</p>
    </div>
  </article>

  <article class="panel">
    <div class="inner">
      <div class="gift">
        <svg viewBox="0 0 52 52"><use href="#badge-ring"/><use href="#ic-coin" x="6" y="6" width="40" height="40"/></svg>
        <div><h3 class="gift__title" style="font-size:10px">Cryptocurrency<br>Strategic &amp; Smart</h3><p class="gift__lead">Consider donating Bitcoin and other cryptocurrencies to your favorite charity.</p></div>
      </div>
      <p class="body" style="font-size:8.8px;line-height:11.8px">Bitcoin and other cryptocurrencies can be donated to charity just like other appreciated assets such as stocks and other business interests. Before you sell bitcoin &amp; donate the after-tax proceeds, consider donating your bitcoin directly to a favorite charity.</p>
      <h4 class="how">How Does It Work?</h4>
      <p class="body">Many donors find it useful to open a Donor-Advised Fund (DAF). This strategy includes two significant benefits, both for you and your favorite charity.</p>
      <ul class="bullets">
        <li><svg class="tick"><use href="#ic-tick"/></svg><span>Your tax deduction will be equal to the fair market value of the donated bitcoin (as determined by a qualified appraisal).</span></li>
        <li><svg class="tick"><use href="#ic-tick"/></svg><span>Your cryptocurrency donation is tax-smart because it may eliminate capital gains taxes on the value / appreciation AND your favorite charity will receive 100% of the value of the contribution.</span></li>
      </ul>
      <p class="body">Often charities are not able to accept direct donations of bitcoin/crypto so using a DAF is a great way to donate these assets.</p>
    </div>
    <div class="photo photo--grandfather" role="img" aria-label="Photo of an elderly man and a young woman sitting together, looking ahead"></div>
    <svg class="curve" style="top:362px" width="229" height="22" viewBox="0 0 229 22" preserveAspectRatio="none"><path d="M0 0 H229 V22 Q114 -2 0 22 Z" fill="#fff"/><path d="M0 22 Q114 -4 229 22" fill="none" stroke="#4cb944" stroke-width="3"/></svg>
  </article>
</section>

</body>
</html>
```